Global Beard Oil Review Business needs a refresh

topwhiskertonic.net is a global business who's mission is to curate all available beard oils from around the world, review and grade them and present this curated collection to the user of the website.

The scope of this job includes the web site design and the design of a suitable logo to be used in the site header.

The existing site can be seen on http://topwhiskertonic.net, however this is a mock-up only the style and logo should NOT be used. This is to give you an idea of the concept of the site only.

This job is for PSD design only.

See attached design brief for detailed design requirements.
Updates

Project Deadline Extended
Reason: Extending deadline by 5 days to allow for final submissions

Target Market(s)

Men's grooming / retail

Industry/Entity Type

Retail

Number of Pages Required

2 page

Font styles to use
Sans Serif

Requirements
Must have
• 1) Comparison Table
• 2) Side Bar
• 3) Header area
• 4) Photo of Delvin Marsk (attached - can be circular or "cut-out")
• 5) Cool beard-oriented custom design background (e.g., stylistic black/brown on brown/orange beard background. I envision this beard background "drawing" rather than photo based)
• (see attached design requirements for details)
Nice to have
• Signature style writing at top with name "Delvin Marsk"
Should not have
• Do NOT use the look & feel or logo from the existing site.

```html
<!DOCTYPE html>
<html lang="en">
<head>
<meta charset="utf-8">
<title>Top Whisker Tonic</title>
<link rel="stylesheet" href="https://fonts.googleapis.com/css2?family=Amatic+SC:wght@400;700&family=Raleway:wght@400;600;700&family=Mr+Dafoe&display=swap">
<style>
:root{
  --orange:#f9a602;
  --maroon:#7d0a0a;
  --maroon-dark:#6a0000;
  --red:#a10d0d;
  --ink:#2b2b2b;
  --muted:#666;
  --line:#e3e3e3;
  --pattern:#e6e6e6;
  --white:#fff;
}
*{box-sizing:border-box;margin:0;padding:0}
html,body{width:1200px;height:2557px;overflow:hidden}
body{font-family:'Raleway',sans-serif;color:var(--ink);background:var(--white)}
.canvas{position:relative;width:1200px;height:2557px;overflow:hidden}
.abs{position:absolute}

/* header */
.site-header{position:absolute;left:0;top:0;width:1200px;height:133px;background:var(--white)}
.brand{position:absolute;left:75px;top:40px;display:flex;align-items:center;gap:10px}
.brand-dot{width:34px;height:34px;border-radius:50%;background:var(--orange)}
.brand-name{font-family:'Amatic SC',cursive;font-weight:700;font-size:40px;color:var(--orange);line-height:1}
.host-photo{position:absolute;left:318px;top:-6px;width:158px;height:158px;border-radius:50%;border:6px solid var(--white);background:radial-gradient(circle at 50% 40%,#8a8a8a,#3c3c3c);box-shadow:0 2px 6px rgba(0,0,0,.35)}
.signature{position:absolute;left:482px;top:22px;font-family:'Mr Dafoe',cursive;font-size:30px;color:var(--ink);transform:rotate(-6deg)}
.contact{position:absolute;left:737px;top:26px;display:flex;align-items:center;gap:12px;font-size:15px}
.contact-icon{width:34px;height:34px;border-radius:50%;background:var(--orange);display:flex;align-items:center;justify-content:center}
.social{position:absolute;display:flex;gap:12px}
.social span{width:27px;height:27px;border-radius:50%;background:var(--orange);display:block}
.social.outline span{background:transparent;border:2px solid var(--white)}
.main-nav{position:absolute;left:530px;top:89px;display:flex;align-items:center;font-size:16px;gap:0}
.main-nav a{color:var(--ink);text-decoration:none;padding:6px 10px}
.main-nav .sep{width:4px;height:4px;border-radius:50%;background:var(--ink);margin:0 6px}
.main-nav a.active{background:var(--maroon);color:var(--white)}

/* hero */
.hero{position:absolute;left:0;top:133px;width:1200px;height:404px;background:linear-gradient(90deg,#3b5a78 0%,#4f6e8c 30%,#9fb4c6 60%,#b9c9d6 100%)}
.hero-title{position:absolute;left:645px;top:80px;font-family:'Amatic SC',cursive;font-weight:700;font-size:74px;line-height:88px;color:#1f1f1f}
.hero-btn{position:absolute;left:646px;top:276px;width:143px;height:53px;background:var(--orange);color:var(--ink);font-size:22px;display:flex;align-items:center;justify-content:center}
.hero-arrow{position:absolute;top:140px}

/* backdrop */
.backdrop{position:absolute;left:0;top:537px;width:1200px;height:1978px;background:var(--pattern)}
.content-panel{position:absolute;left:57px;top:537px;width:1083px;height:1978px;background:var(--white)}

/* welcome */
.welcome-title{position:absolute;left:0;top:572px;width:1200px;text-align:center;font-family:'Amatic SC',cursive;font-weight:700;font-size:62px;color:var(--ink)}
.welcome-title em{font-style:normal;color:var(--maroon)}
.welcome-text{position:absolute;left:155px;top:650px;width:890px;text-align:center;font-size:12.5px;line-height:21px;color:var(--ink)}
.step-circle{position:absolute;width:108px;height:108px;border-radius:50%;background:var(--orange);display:flex;align-items:center;justify-content:center}
.step-label{position:absolute;width:200px;text-align:center;font-family:'Amatic SC',cursive;font-weight:700;font-size:30px}
.tooltip{position:absolute;left:500px;top:948px;width:125px;height:26px;background:#9a9a9a;color:var(--white);font-size:12px;display:flex;align-items:center;justify-content:center}

/* table */
.compare-table{position:absolute;left:80px;top:987px;width:737px;height:1500px;border:1px solid var(--line);border-top:0;border-radius:0 0 6px 6px}
.table-head{position:absolute;left:-1px;top:0;width:739px;height:60px;background:var(--red);border-radius:5px 5px 0 0;overflow:hidden}
.head-key{position:absolute;left:0;top:0;width:332px;height:60px;background:var(--maroon-dark)}
.head-cell{position:absolute;top:10px;color:var(--orange);font-size:12px;font-weight:700}
.head-cell .val{display:block;margin-top:5px;color:var(--white);font-weight:400;font-size:12.5px;border-bottom:1px solid rgba(255,255,255,.6);padding-bottom:2px;width:70px}
.head-cell.active{text-decoration:underline}
.oil-row{position:absolute;left:0;width:735px;height:99px;border-bottom:1px solid var(--line)}
.oil-thumb{position:absolute;left:17px;top:18px;width:44px;height:62px;background:linear-gradient(#c77a2e,#5b2e10);border-radius:4px}
.oil-thumb.boxed{width:62px;background:linear-gradient(#f3d37a,#e6a21c)}
.oil-name{position:absolute;left:118px;top:16px;font-size:16px;font-weight:700;color:var(--maroon)}
.oil-name span{font-weight:400;color:var(--ink)}
.f{position:absolute;font-size:11.5px;color:var(--ink)}
.f b{color:var(--orange);font-weight:700}
.buy-btn{position:absolute;left:626px;top:22px;width:82px;height:30px;background:var(--orange);color:var(--white);font-size:15px;display:flex;align-items:center;justify-content:center}
.load-more{position:absolute;left:287px;top:1443px;width:170px;height:36px;background:#ddd;color:var(--white);font-size:18px;display:flex;align-items:center;justify-content:center;border-radius:3px}

/* sidebar */
.newsletter{position:absolute;left:855px;top:987px;width:265px;height:343px;background:var(--orange);text-align:center}
.newsletter h3{font-family:'Amatic SC',cursive;font-weight:700;font-size:37px;line-height:50px;color:var(--maroon);margin-top:16px}
.newsletter p{font-size:12.5px;line-height:19px;margin:10px 18px 0}
.email-field{margin:20px auto 0;width:222px;height:36px;background:var(--white);font-size:12px;color:#888;display:flex;align-items:center;justify-content:center}
.signup-btn{margin:12px auto 0;width:222px;height:36px;background:var(--maroon);color:var(--white);font-size:13px;font-weight:700;display:flex;align-items:center;justify-content:center}
.newsletter small{display:block;margin:18px 30px 0;font-size:10.5px;color:var(--white);line-height:15px}
.blog-title{position:absolute;left:855px;top:1375px;font-family:'Amatic SC',cursive;font-weight:700;font-size:40px;color:var(--maroon)}
.post{position:absolute;left:855px;width:265px}
.post-image{width:265px;height:155px;border-radius:4px}
.post h4{margin-top:12px;font-size:16px;color:var(--orange);font-weight:700}
.post time{display:block;margin-top:9px;font-size:12px;color:var(--ink)}

/* footer */
.site-footer{position:absolute;left:0;top:2515px;width:1200px;height:42px;background:var(--orange)}
.site-footer p{position:absolute;left:80px;top:13px;font-size:12.5px;color:var(--white)}
</style>
</head>
<body>
<div class="canvas">

<header class="site-header">
  <div class="brand"><span class="brand-dot"></span><span class="brand-name">Top Whisker Tonic</span></div>
  <div class="host-photo" role="img" aria-label="Portrait photo of Delvin Marsk"></div>
  <div class="signature">-With Delvin Marsk</div>
  <div class="contact">
    <span class="contact-icon"><svg width="16" height="16" viewBox="0 0 24 24"><path d="M6.6 10.8a15 15 0 0 0 6.6 6.6l2.2-2.2c.3-.3.7-.4 1-.2 1.1.4 2.3.6 3.6.6.6 0 1 .4 1 1V20c0 .6-.4 1-1 1A17 17 0 0 1 3 4c0-.6.4-1 1-1h3.5c.6 0 1 .4 1 1 0 1.3.2 2.5.6 3.6.1.3 0 .7-.2 1z" fill="#6a0000"/></svg></span>
    <span>info@topwhiskertonic.net</span>
  </div>
  <div class="social" style="left:983px;top:30px"><span></span><span></span><span></span><span></span></div>
  <nav class="main-nav">
    <a class="active">Home</a>
    <a>About</a><span class="sep"></span>
    <a>Our Charter</a><span class="sep"></span>
    <a>Beard Oil Review Methodology</a><span class="sep"></span>
    <a>Blog</a>
  </nav>
</header>

<section class="hero" role="img" aria-label="Photo of a bearded man in a denim shirt against a textured wall">
  <h1 class="hero-title">Curate, Review &amp; Grade<br>Then Present</h1>
  <div class="hero-btn">See Table</div>
  <svg class="hero-arrow" style="left:22px" width="32" height="110" viewBox="0 0 32 110"><polyline points="28,2 4,55 28,108" fill="none" stroke="#fff" stroke-width="3"/></svg>
  <svg class="hero-arrow" style="left:1148px" width="32" height="110" viewBox="0 0 32 110"><polyline points="4,2 28,55 4,108" fill="none" stroke="#fff" stroke-width="3"/></svg>
</section>

<div class="backdrop" role="img" aria-label="Light grey pattern of drawn bearded faces"></div>
<main class="content-panel"></main>

<h2 class="welcome-title">Welcome To <em>Top Whisker Tonic</em></h2>
<p class="welcome-text">We are a global business with the mission is to curate all available beard oils from around the world, review &amp; grade them &amp; present this curated collection to the users of the site. Our Target Audience are all grooming men. Lorem ipsum dolor sit amet, consectetuer adipiscing elit, sed diam nonummy nibh euismod tincidunt ut laoreet dolore magna aliquam erat volutpat. Lorem ipsum dolor sit amet, consectetuer adipiscing elit, sed diam nonummy nibh euismod tincidunt ut laoreet dolore magna aliquam erat volutpat.</p>

<svg class="abs" style="left:0;top:740px" width="1200" height="200" viewBox="0 0 1200 200">
  <path id="arc1" d="M285 115 Q420 200 545 105" fill="none" stroke="#555" stroke-width="1.5" stroke-dasharray="2 4"/>
  <path id="arc2" d="M655 80 Q790 10 915 80" fill="none" stroke="#555" stroke-width="1.5" stroke-dasharray="2 4"/>
  <path d="M908 74 l8 7 -10 2" fill="none" stroke="#555" stroke-width="1.5"/>
  <text font-family="Raleway,sans-serif" font-size="13" fill="#7d0a0a"><textPath href="#arc1" startOffset="12%">We curate all available beard oils</textPath></text>
  <text font-family="Raleway,sans-serif" font-size="13" fill="#7d0a0a"><textPath href="#arc2" startOffset="6%">Review &amp; Grade them &amp; Present</textPath></text>
</svg>

<div class="step-circle" style="left:172px;top:781px">
  <svg width="48" height="48" viewBox="0 0 48 48"><polyline points="8,25 19,36 40,12" fill="none" stroke="#6a0000" stroke-width="6"/></svg>
</div>
<div class="step-circle" style="left:546px;top:781px">
  <svg width="52" height="52" viewBox="0 0 24 24"><path d="M12 2l3 6.6 7.2.7-5.4 4.8 1.6 7.1L12 17.5 5.6 21.2l1.6-7.1L1.8 9.3 9 8.6z" fill="#6a0000"/></svg>
</div>
<div class="step-circle" style="left:919px;top:781px">
  <svg width="54" height="54" viewBox="0 0 48 48"><rect x="5" y="8" width="38" height="30" rx="3" fill="none" stroke="#6a0000" stroke-width="4"/><line x1="5" y1="15" x2="43" y2="15" stroke="#6a0000" stroke-width="3"/><path d="M24 36V21m-7 7l7-7 7 7" fill="none" stroke="#6a0000" stroke-width="4"/></svg>
</div>
<div class="step-label" style="left:126px;top:897px">Curate</div>
<div class="step-label" style="left:500px;top:897px">Review &amp; Grade</div>
<div class="step-label" style="left:873px;top:897px">Present</div>

<div class="tooltip">Therapeutic Affect</div>

<section class="compare-table">
  <div class="table-head">
    <div class="head-key"></div>
    <div class="head-cell" style="left:16px">ORIGIN &#9662;<span class="val">USA</span></div>
    <div class="head-cell" style="left:114px">BASE OIL &#9662;<span class="val">Lorem Ipsum</span></div>
    <div class="head-cell" style="left:227px">SCENT &#9662;<span class="val">Lorem Ipsum</span></div>
    <div class="head-cell" style="left:349px">AROMA &#9662;<span class="val">7</span></div>
    <div class="head-cell active" style="left:444px">TH. AFFECT &#9662;<span class="val">5</span></div>
    <div class="head-cell" style="left:556px">VALUE &#9662;<span class="val">5</span></div>
    <div class="head-cell" style="left:642px">OVER ALL &#9662;<span class="val">5</span></div>
  </div>

  <div class="oil-row" style="top:62px"><div class="oil-thumb boxed" role="img" aria-label="Boxed beard oil bottle"></div><div class="oil-name">Ridgeline-Trail-Blend- <span>by Rugged Ronin</span></div><div class="f" style="left:118px;top:45px"><b>Origin:</b> USA</div><div class="f" style="left:218px;top:45px"><b>Base Oil:</b> Jojoba, Hempseed</div><div class="f" style="left:407px;top:45px"><b>Scent:</b> Spice Bazaar</div><div class="f" style="left:118px;top:70px"><b>Aroma:</b> 7</div><div class="f" style="left:218px;top:70px"><b>Therapeutic Affect:</b> 5</div><div class="f" style="left:407px;top:70px"><b>Value:</b> 5</div><div class="f" style="left:502px;top:70px"><b>Over All:</b> 5</div><div class="buy-btn">Buy Now</div></div>
  <div class="oil-row" style="top:161px"><div class="oil-thumb" role="img" aria-label="Beard oil bottle"></div><div class="oil-name">Harbor Street Tobacco- <span>by Rugged Ronin</span></div><div class="f" style="left:118px;top:45px"><b>Origin:</b> USA</div><div class="f" style="left:218px;top:45px"><b>Base Oil:</b> Jojoba, Hempseed</div><div class="f" style="left:407px;top:45px"><b>Scent:</b> Spice Bazaar</div><div class="f" style="left:118px;top:70px"><b>Aroma:</b> 7</div><div class="f" style="left:218px;top:70px"><b>Therapeutic Affect:</b> 5</div><div class="f" style="left:407px;top:70px"><b>Value:</b> 5</div><div class="f" style="left:502px;top:70px"><b>Over All:</b> 5</div><div class="buy-btn">Buy Now</div></div>
  <div class="oil-row" style="top:260px"><div class="oil-thumb" role="img" aria-label="Beard oil bottle"></div><div class="oil-name">The Whiskered Gent Original- <span>by Rugged Ronin</span></div><div class="f" style="left:118px;top:45px"><b>Origin:</b> USA</div><div class="f" style="left:218px;top:45px"><b>Base Oil:</b> Jojoba, Hempseed</div><div class="f" style="left:407px;top:45px"><b>Scent:</b> Spice Bazaar</div><div class="f" style="left:118px;top:70px"><b>Aroma:</b> 7</div><div class="f" style="left:218px;top:70px"><b>Therapeutic Affect:</b> 5</div><div class="f" style="left:407px;top:70px"><b>Value:</b> 5</div><div class="f" style="left:502px;top:70px"><b>Over All:</b> 5</div><div class="buy-btn">Buy Now</div></div>
  <div class="oil-row" style="top:359px"><div class="oil-thumb" role="img" aria-label="Beard oil bottle"></div><div class="oil-name">Oakmoss Spiced Citrus- <span>by Rugged Ronin</span></div><div class="f" style="left:118px;top:45px"><b>Origin:</b> USA</div><div class="f" style="left:218px;top:45px"><b>Base Oil:</b> Jojoba, Hempseed</div><div class="f" style="left:407px;top:45px"><b>Scent:</b> Spice Bazaar</div><div class="f" style="left:118px;top:70px"><b>Aroma:</b> 7</div><div class="f" style="left:218px;top:70px"><b>Therapeutic Affect:</b> 5</div><div class="f" style="left:407px;top:70px"><b>Value:</b> 5</div><div class="f" style="left:502px;top:70px"><b>Over All:</b> 5</div><div class="buy-btn">Buy Now</div></div>
  <div class="oil-row" style="top:458px"><div class="oil-thumb" role="img" aria-label="Beard oil bottle"></div><div class="oil-name">Harbor Street Tobacco- <span>by Rugged Ronin</span></div><div class="f" style="left:118px;top:45px"><b>Origin:</b> USA</div><div class="f" style="left:218px;top:45px"><b>Base Oil:</b> Jojoba, Hempseed</div><div class="f" style="left:407px;top:45px"><b>Scent:</b> Spice Bazaar</div><div class="f" style="left:118px;top:70px"><b>Aroma:</b> 7</div><div class="f" style="left:218px;top:70px"><b>Therapeutic Affect:</b> 5</div><div class="f" style="left:407px;top:70px"><b>Value:</b> 5</div><div class="f" style="left:502px;top:70px"><b>Over All:</b> 5</div><div class="buy-btn">Buy Now</div></div>
  <div class="oil-row" style="top:557px"><div class="oil-thumb" role="img" aria-label="Beard oil bottle"></div><div class="oil-name">The Whiskered Gent Original- <span>by Rugged Ronin</span></div><div class="f" style="left:118px;top:45px"><b>Origin:</b> USA</div><div class="f" style="left:218px;top:45px"><b>Base Oil:</b> Jojoba, Hempseed</div><div class="f" style="left:407px;top:45px"><b>Scent:</b> Spice Bazaar</div><div class="f" style="left:118px;top:70px"><b>Aroma:</b> 7</div><div class="f" style="left:218px;top:70px"><b>Therapeutic Affect:</b> 5</div><div class="f" style="left:407px;top:70px"><b>Value:</b> 5</div><div class="f" style="left:502px;top:70px"><b>Over All:</b> 5</div><div class="buy-btn">Buy Now</div></div>
  <div class="oil-row" style="top:656px"><div class="oil-thumb boxed" role="img" aria-label="Boxed beard oil bottle"></div><div class="oil-name">Ridgeline-Trail-Blend- <span>by Rugged Ronin</span></div><div class="f" style="left:118px;top:45px"><b>Origin:</b> USA</div><div class="f" style="left:218px;top:45px"><b>Base Oil:</b> Jojoba, Hempseed</div><div class="f" style="left:407px;top:45px"><b>Scent:</b> Spice Bazaar</div><div class="f" style="left:118px;top:70px"><b>Aroma:</b> 7</div><div class="f" style="left:218px;top:70px"><b>Therapeutic Affect:</b> 5</div><div class="f" style="left:407px;top:70px"><b>Value:</b> 5</div><div class="f" style="left:502px;top:70px"><b>Over All:</b> 5</div><div class="buy-btn">Buy Now</div></div>
  <div class="oil-row" style="top:755px"><div class="oil-thumb" role="img" aria-label="Beard oil bottle"></div><div class="oil-name">Harbor Street Tobacco- <span>by Rugged Ronin</span></div><div class="f" style="left:118px;top:45px"><b>Origin:</b> USA</div><div class="f" style="left:218px;top:45px"><b>Base Oil:</b> Jojoba, Hempseed</div><div class="f" style="left:407px;top:45px"><b>Scent:</b> Spice Bazaar</div><div class="f" style="left:118px;top:70px"><b>Aroma:</b> 7</div><div class="f" style="left:218px;top:70px"><b>Therapeutic Affect:</b> 5</div><div class="f" style="left:407px;top:70px"><b>Value:</b> 5</div><div class="f" style="left:502px;top:70px"><b>Over All:</b> 5</div><div class="buy-btn">Buy Now</div></div>
  <div class="oil-row" style="top:854px"><div class="oil-thumb" role="img" aria-label="Beard oil bottle"></div><div class="oil-name">The Whiskered Gent Original- <span>by Rugged Ronin</span></div><div class="f" style="left:118px;top:45px"><b>Origin:</b> USA</div><div class="f" style="left:218px;top:45px"><b>Base Oil:</b> Jojoba, Hempseed</div><div class="f" style="left:407px;top:45px"><b>Scent:</b> Spice Bazaar</div><div class="f" style="left:118px;top:70px"><b>Aroma:</b> 7</div><div class="f" style="left:218px;top:70px"><b>Therapeutic Affect:</b> 5</div><div class="f" style="left:407px;top:70px"><b>Value:</b> 5</div><div class="f" style="left:502px;top:70px"><b>Over All:</b> 5</div><div class="buy-btn">Buy Now</div></div>
  <div class="oil-row" style="top:953px"><div class="oil-thumb" role="img" aria-label="Beard oil bottle"></div><div class="oil-name">Oakmoss Spiced Citrus- <span>by Rugged Ronin</span></div><div class="f" style="left:118px;top:45px"><b>Origin:</b> USA</div><div class="f" style="left:218px;top:45px"><b>Base Oil:</b> Jojoba, Hempseed</div><div class="f" style="left:407px;top:45px"><b>Scent:</b> Spice Bazaar</div><div class="f" style="left:118px;top:70px"><b>Aroma:</b> 7</div><div class="f" style="left:218px;top:70px"><b>Therapeutic Affect:</b> 5</div><div class="f" style="left:407px;top:70px"><b>Value:</b> 5</div><div class="f" style="left:502px;top:70px"><b>Over All:</b> 5</div><div class="buy-btn">Buy Now</div></div>
  <div class="oil-row" style="top:1052px"><div class="oil-thumb" role="img" aria-label="Beard oil bottle"></div><div class="oil-name">Harbor Street Tobacco- <span>by Rugged Ronin</span></div><div class="f" style="left:118px;top:45px"><b>Origin:</b> USA</div><div class="f" style="left:218px;top:45px"><b>Base Oil:</b> Jojoba, Hempseed</div><div class="f" style="left:407px;top:45px"><b>Scent:</b> Spice Bazaar</div><div class="f" style="left:118px;top:70px"><b>Aroma:</b> 7</div><div class="f" style="left:218px;top:70px"><b>Therapeutic Affect:</b> 5</div><div class="f" style="left:407px;top:70px"><b>Value:</b> 5</div><div class="f" style="left:502px;top:70px"><b>Over All:</b> 5</div><div class="buy-btn">Buy Now</div></div>
  <div class="oil-row" style="top:1151px"><div class="oil-thumb" role="img" aria-label="Beard oil bottle"></div><div class="oil-name">The Whiskered Gent Original- <span>by Rugged Ronin</span></div><div class="f" style="left:118px;top:45px"><b>Origin:</b> USA</div><div class="f" style="left:218px;top:45px"><b>Base Oil:</b> Jojoba, Hempseed</div><div class="f" style="left:407px;top:45px"><b>Scent:</b> Spice Bazaar</div><div class="f" style="left:118px;top:70px"><b>Aroma:</b> 7</div><div class="f" style="left:218px;top:70px"><b>Therapeutic Affect:</b> 5</div><div class="f" style="left:407px;top:70px"><b>Value:</b> 5</div><div class="f" style="left:502px;top:70px"><b>Over All:</b> 5</div><div class="buy-btn">Buy Now</div></div>
  <div class="oil-row" style="top:1250px;border-bottom:0"><div class="oil-thumb boxed" role="img" aria-label="Boxed beard oil bottle"></div><div class="oil-name">Ridgeline-Trail-Blend- <span>by Rugged Ronin</span></div><div class="f" style="left:118px;top:45px"><b>Origin:</b> USA</div><div class="f" style="left:218px;top:45px"><b>Base Oil:</b> Jojoba, Hempseed</div><div class="f" style="left:407px;top:45px"><b>Scent:</b> Spice Bazaar</div><div class="f" style="left:118px;top:70px"><b>Aroma:</b> 7</div><div class="f" style="left:218px;top:70px"><b>Therapeutic Affect:</b> 5</div><div class="f" style="left:407px;top:70px"><b>Value:</b> 5</div><div class="f" style="left:502px;top:70px"><b>Over All:</b> 5</div><div class="buy-btn">Buy Now</div></div>

  <div class="load-more">Loading More...</div>
</section>

<aside>
  <div class="newsletter">
    <h3>Get More Stuff Like<br>This In Your InBox</h3>
    <p>Subscribe to our mailing list &amp; get interesting stuff &amp; updates.</p>
    <div class="email-field">Enter your email here</div>
    <div class="signup-btn">SIGNUP NOW</div>
    <small>We respect your privacy and take protecting it seriously</small>
  </div>
  <h3 class="blog-title">Latest Blog</h3>
  <article class="post" style="top:1452px"><div class="post-image" role="img" aria-label="Bearded man beside a beard oil poster" style="background:linear-gradient(90deg,#4a4a4a,#b8b2a6)"></div><h4>How to Use Juniper's Beard Oil</h4><time>February 12, 2016</time></article>
  <article class="post" style="top:1710px"><div class="post-image" role="img" aria-label="Dried herbs, oil bottle and mortar on wood" style="background:linear-gradient(135deg,#c9a06a,#7a5b3a)"></div><h4>How to Use Juniper's Beard Oil</h4><time>February 12, 2016</time></article>
  <article class="post" style="top:1958px"><div class="post-image" role="img" aria-label="Bearded man with a pipe outdoors" style="background:linear-gradient(135deg,#e8dcc0,#8c7a52)"></div><h4>How to Use Juniper's Beard Oil</h4><time>February 12, 2016</time></article>
  <article class="post" style="top:2208px"><div class="post-image" role="img" aria-label="Man trimming his beard with a trimmer" style="background:linear-gradient(135deg,#cfe6f2,#7aa8c4)"></div><h4>How to Use Juniper's Beard Oil</h4><time>February 12, 2016</time></article>
</aside>

<footer class="site-footer">
  <p>Copyright 2016 Top Whisker Tonic. All Rights Reserved.</p>
  <div class="social outline" style="left:983px;top:7px"><span></span><span></span><span></span><span></span></div>
</footer>

</div>
</body>
</html>
```